Construction company stationary design

We're wanting to develop a new professional stationary set for a newly establised property related business using our existing logo (attached). Business incorporates renovations, property investment and property development.

Specifically needing letter head, business cards, envelopes, email signature and need to get tshirt and caps embroydered.

Looking for something quite modern but professional using white, black and green.

Investment

```html
<!DOCTYPE html>
<html lang="en">
<head>
<meta charset="utf-8">
<title>Torvane Builders – Stationery Set</title>
<link href="https://fonts.googleapis.com/css2?family=Questrial&family=Source+Sans+3:wght@400&display=swap" rel="stylesheet">
<style>
  :root {
    --green: #7dc242;
    --green-soft: #eef5e6;
    --black: #141414;
    --white: #ffffff;
    --ink: #3a3a3a;
    --rule: #8a8a8a;
    --backdrop: #c98a55;
    --fabric-light: #f1f1f1;
    --fabric-shade: #d9d9d9;
  }
  * { box-sizing: border-box; margin: 0; padding: 0; }
  html, body { width: 1200px; height: 514px; overflow: hidden; }
  body {
    position: relative;
    background: var(--backdrop);
    font-family: "Questrial", "Century Gothic", sans-serif;
    color: var(--ink);
  }
  .piece { position: absolute; background: var(--white); overflow: hidden; }
  .brand { color: var(--green); font-weight: 400; line-height: 1; white-space: nowrap; }

  /* Letterheads */
  .letterhead { top: 18px; width: 211px; height: 272px; }
  .letterhead--one { left: 4px; }
  .letterhead--two { left: 243px; }
  .letterhead--fax { left: 478px; }
  .letterhead .brand { position: absolute; top: 30px; font-size: 12px; }
  .letterhead--one .brand, .letterhead--two .brand { left: 70px; }
  .letterhead--fax .brand { left: 13px; }
  .contact-block {
    position: absolute; top: 17px; right: 10px;
    border-left: 1px solid var(--rule); padding-left: 3px;
    font-size: 4px; line-height: 6px; color: var(--ink); white-space: nowrap;
  }
  .contact-block .dot { display: inline-block; width: 3px; height: 3px; background: var(--green); margin-right: 2px; }
  .page-footer {
    position: absolute; left: 0; right: 0; bottom: 0; height: 11px;
    border-top: 1px solid var(--rule); padding-top: 2px;
  }
  .page-footer .band {
    height: 8px; background: var(--green); color: var(--white);
    font-size: 4px; line-height: 8px; text-align: center; white-space: nowrap;
  }
  .watermark {
    position: absolute; left: 0; right: 0; text-align: center;
    color: var(--green-soft); font-size: 30px;
  }
  .letterhead--one .watermark { top: 120px; }
  .letterhead--two .watermark { top: 150px; }
  .option-label {
    position: absolute; top: 296px; width: 211px; text-align: center;
    font-family: "Source Sans 3", sans-serif; font-size: 16px; color: var(--white);
  }

  /* Fax */
  .fax-title { position: absolute; left: 14px; top: 66px; font-size: 13px; font-weight: 400; color: var(--black); }
  .fax-fields { position: absolute; left: 14px; right: 18px; top: 87px; }
  .fax-row { display: flex; border-bottom: 1px solid var(--rule); height: 11px; font-size: 4px; align-items: flex-end; padding-bottom: 1px; }
  .fax-row span { flex: 1; }
  .fax-checks { position: absolute; left: 14px; right: 14px; top: 140px; display: flex; justify-content: space-between; font-size: 4px; white-space: nowrap; }
  .fax-checks span::before { content: ""; display: inline-block; width: 4px; height: 4px; border: 1px solid var(--ink); margin-right: 3px; vertical-align: middle; }

  /* Business cards */
  .card { height: 74px; }
  .card--front { left: 730px; top: 4px; width: 130px; }
  .card--alt { left: 888px; top: 12px; width: 166px; }
  .card .brand { position: absolute; font-size: 11px; }
  .card--front .brand { left: 14px; top: 30px; }
  .card--front .card-details { position: absolute; left: 74px; top: 12px; border-left: 1px solid var(--rule); padding-left: 4px; font-size: 4px; line-height: 6px; white-space: nowrap; }
  .card-details .name { color: var(--green); font-size: 5px; margin-bottom: 2px; }
  .card--alt .brand { left: 10px; top: 26px; }
  .card--alt .card-lines { position: absolute; left: 10px; top: 50px; font-size: 4px; line-height: 6px; white-space: nowrap; }
  .card--alt .name { position: absolute; right: 10px; top: 50px; color: var(--green); font-size: 7px; }
  .card-band { position: absolute; left: 0; right: 0; bottom: 0; height: 9px; border-top: 1px solid var(--rule); padding-top: 1px; }
  .card-band div { height: 7px; background: var(--green); color: var(--white); font-size: 4px; line-height: 7px; padding-left: 8px; white-space: nowrap; }
  .card--back { left: 734px; top: 96px; width: 129px; height: 73px; background: var(--green); }
  .card--back .brand { color: var(--white); position: absolute; left: 0; right: 0; top: 28px; text-align: center; font-size: 12px; }
  .card--back .web { position: absolute; left: 0; right: 0; bottom: 6px; text-align: center; color: var(--white); font-size: 5px; letter-spacing: 1px; }

  /* Envelopes */
  .envelope { left: 708px; top: 179px; width: 236px; height: 105px; }
  .envelope .brand { position: absolute; left: 12px; top: 20px; font-size: 10px; }
  .envelope .faint-name { position: absolute; right: 12px; top: 66px; font-size: 8px; color: var(--green-soft); }
  .envelope-backs { position: absolute; left: 960px; top: 106px; width: 166px; height: 206px; }
  .envelope-backs text { font-size: 6px; }

  /* Apparel placeholders */
  .apparel { position: absolute; }
  .apparel--tee { left: 46px; top: 342px; width: 122px; height: 162px;
    background: linear-gradient(180deg, var(--fabric-light), var(--fabric-shade)); }
  .apparel--cap-front { left: 197px; top: 344px; width: 165px; height: 160px;
    background: linear-gradient(180deg, var(--black) 0%, #2a2a2a 70%, var(--green) 100%); }
  .apparel--cap-back { left: 381px; top: 352px; width: 209px; height: 136px;
    background: linear-gradient(180deg, var(--black) 0%, #2a2a2a 75%, var(--green) 100%); }
  svg text { font-family: "Questrial", "Century Gothic", sans-serif; }
</style>
</head>
<body>

  <!-- Letterhead option 1 -->
  <section class="piece letterhead letterhead--one">
    <div class="brand">Torvane Builders</div>
    <div class="contact-block">12 Ridge Lane<br>Oakfield 4021</div>
    <div class="watermark">Torvane</div>
    <div class="page-footer"><div class="band">0123 480 915 · hello@torvane.com · www.torvane.com</div></div>
  </section>
  <p class="option-label" style="left:4px">Option-1</p>

  <!-- Letterhead option 2 -->
  <section class="piece letterhead letterhead--two">
    <div class="brand">Torvane Builders</div>
    <div class="contact-block">
      <span class="dot"></span>0123 480 915<br>
      <span class="dot"></span>hello@torvane.com<br>
      <span class="dot"></span>www.torvane.com
    </div>
    <div class="watermark">Torvane</div>
    <div class="page-footer"><div class="band">12 Ridge Lane, Oakfield 4021</div></div>
  </section>
  <p class="option-label" style="left:243px">Option-2</p>

  <!-- Fax sheet option 3 -->
  <section class="piece letterhead letterhead--fax">
    <div class="brand">Torvane Builders</div>
    <div class="contact-block">
      <span class="dot"></span>0123 480 915<br>
      <span class="dot"></span>hello@torvane.com<br>
      <span class="dot"></span>www.torvane.com
    </div>
    <h1 class="fax-title">FAX</h1>
    <div class="fax-fields">
      <div class="fax-row"><span>To :</span><span>From :</span></div>
      <div class="fax-row"><span>Fax :</span><span>Pages :</span></div>
      <div class="fax-row"><span>Phone :</span><span>Date :</span></div>
      <div class="fax-row"><span>Re :</span><span>CC :</span></div>
    </div>
    <div class="fax-checks">
      <span>Urgent</span><span>For Review</span><span>Please Comment</span><span>Please Reply</span><span>Please Recycle</span>
    </div>
    <div class="page-footer"><div class="band">12 Ridge Lane, Oakfield 4021</div></div>
  </section>
  <p class="option-label" style="left:478px">Option-3</p>

  <!-- Business cards -->
  <section class="piece card card--front">
    <div class="brand">Torvane</div>
    <div class="card-details">
      <div class="name">PERSONS NAME</div>
      0123 480 915<br>0123 480 916<br>hello@torvane.com<br>www.torvane.com
    </div>
    <div class="card-band"><div>12 Ridge Lane, Oakfield 4021</div></div>
  </section>

  <section class="piece card card--alt">
    <div class="brand">Torvane Builders</div>
    <div class="card-lines">0123 480 915 · 0123 480 916<br>hello@torvane.com · www.torvane.com</div>
    <div class="name">PERSONS NAME</div>
    <div class="card-band"><div>12 Ridge Lane, Oakfield 4021</div></div>
  </section>

  <section class="piece card--back">
    <div class="brand">Torvane Builders</div>
    <div class="web">www.torvane.com</div>
  </section>

  <!-- DL envelope front -->
  <section class="piece envelope">
    <div class="brand">Torvane Builders</div>
    <div class="faint-name">Torvane</div>
    <div class="page-footer"><div class="band">12 Ridge Lane, Oakfield 4021</div></div>
  </section>

  <!-- Envelope backs -->
  <svg class="envelope-backs" viewBox="0 0 166 206" aria-label="Envelope flap variations">
    <rect x="0" y="0" width="166" height="206" fill="var(--white)"/>
    <path d="M0 102 L0 122 Q83 150 166 122 L166 102" fill="var(--white)" stroke="var(--ink)" stroke-width="0.6"/>
    <text x="83" y="124" text-anchor="middle" fill="var(--green)">Torvane</text>
    <path d="M0 52 L0 72 Q83 102 166 72 L166 52 Z" fill="var(--green)"/>
    <text x="83" y="76" text-anchor="middle" fill="var(--white)">Torvane</text>
    <path d="M0 0 L0 20 Q83 52 166 20 L166 0 Z" fill="var(--black)"/>
    <text x="83" y="24" text-anchor="middle" fill="var(--white)">Torvane</text>
  </svg>

  <!-- Apparel -->
  <div class="apparel apparel--tee" role="img" aria-label="White crew-neck tee with green trim and the company name printed in green on the chest"></div>
  <div class="apparel apparel--cap-front" role="img" aria-label="Black cap, front view, with green and white peak trim and the company name embroidered in green"></div>
  <div class="apparel apparel--cap-back" role="img" aria-label="Black cap, back view, with green strap band and small green embroidery"></div>

</body>
</html>
```